Spanish Student Needs a Cover for his PhD Dissertation

Hi everyone :) So, I'm a Corneal surgeon currently finishing my PhD, with a dissertation focused on the evaluation of quality of life in patients affected by a disease called Keratoconus. Just so you know, Keratoconus is a condition in which the cornea (the frontal part of the way) gets thin and bulgy and it decreases vision. What I did during my PhD was designing a questionnaire for evaluating quality of life in this kind of patients.
I need to design a hard cover for my dissertation, which is 200 sheets long. I like kind of minimalistic and geometric designs but I am totally open to suggestions. What needs to be in the cover is the name of the dissertation "Diseño, desarrollo y validación de una encuesta para evaluar el compromiso visual y emocional subjetivos en pacientes con Queratocono" and my name, "Iker Zurmendi". The other thing that needs to go there is the logo of my university (Universidad de Montehierro). Aside from that, anything else is up to the designer. It would be important to use the kind of "red" color I am using in the dissertation. I am attaching the frontal page of my dissertation so you know what kind of design and colors I am using.
In the back part, of the cover, there should be this small inscription: "Iker Zurmendi, MD, es un Oftalmólogo Subespecialista en Cirugía Refractiva de la Universidad Tecnológica Cordillerana (Colombia) y la Universidad de Montehierro (España). Actualmente se desempeña como miembro del Departamento de Córnea y Cirugía Refractiva de la Clínica de Oftalmología Miraluz y como director de su propia compañía de emprendimiento médico Silver Heron Surgical". Please leave a space to place my picture; I will have it taken this week so I don't have it right now, you can just leave the blank spot and I will include it later
The size of the pages is standard "letter" size.
Thanks a lot!

Target Market(s)

PhD Scholars

Font styles to use
Serif

Requirements
Must have
• The "red" color I use on my font. It must be formal but "young".
Nice to have
• I like to keep the design clean, kind of "formal with a young" touch so to speak. I really like gray colors, so it would be nice to have broad areas of gray. I love geometrical designs.
I have uploaded a very early version a friend of mine made (it even had a different title); this can be a starting point for you to work on, but I am more than open to suggestions and new ideas.
Should not have
• Please don't use my whole name, Iker Zurmendi is fine. I don't like ALL CAPITALS.

```html
<!DOCTYPE html>
<html lang="es">
<head>
<meta charset="utf-8">
<title>Cubierta de tesis doctoral – Iker Zurmendi</title>
<link href="https://fonts.googleapis.com/css2?family=Crimson+Pro:wght@400;600&family=Montserrat:wght@800&family=Playfair+Display+SC:wght@700&display=swap" rel="stylesheet">
<style>
  :root {
    --crimson: #ab1e41;
    --crimson-deep: #7b2b3b;
    --charcoal: #252525;
    --slate: #808080;
    --silver: #c9c9c9;
    --paper: #ffffff;
    --ink: #1e1e1e;
  }
  html, body {
    margin: 0;
    padding: 0;
    width: 1200px;
    height: 930px;
    overflow: hidden;
    background: var(--paper);
  }
  .sheet {
    position: relative;
    width: 1200px;
    height: 930px;
  }
  .side-label {
    position: absolute;
    margin: 0;
    font-family: "Crimson Pro", Georgia, serif;
    font-weight: 400;
    font-size: 21px;
    color: var(--crimson);
    transform: translateX(-50%);
  }
  .side-label--front { left: 320px; top: 52px; }
  .side-label--back  { left: 904px; top: 59px; }
  .cover {
    position: absolute;
    display: block;
    filter: drop-shadow(6px 8px 7px rgba(0,0,0,0.55));
  }
  .cover--front { left: 54px; top: 113px; width: 534px; height: 691px; }
  .cover--back  { left: 612px; top: 113px; width: 535px; height: 694px; }
  .title-text {
    font-family: "Playfair Display SC", Georgia, serif;
    font-weight: 700;
    font-size: 44px;
    fill: var(--paper);
  }
  .author-spine {
    font-family: "Montserrat", Arial, sans-serif;
    font-weight: 800;
    font-size: 48px;
    fill: var(--silver);
  }
  .institution-name {
    font-family: "Crimson Pro", Georgia, serif;
    font-weight: 600;
    font-size: 33px;
    fill: var(--paper);
  }
  .school-name {
    font-family: "Crimson Pro", Georgia, serif;
    font-weight: 600;
    font-size: 27px;
    fill: var(--ink);
  }
  .bio-text {
    font-family: "Crimson Pro", Georgia, serif;
    font-weight: 400;
    font-size: 30px;
    fill: var(--paper);
  }
  .photo-hint {
    font-family: "Crimson Pro", Georgia, serif;
    font-weight: 400;
    font-size: 31px;
    fill: var(--ink);
  }
</style>
</head>
<body>
<main class="sheet">
  <h2 class="side-label side-label--front">Front</h2>
  <h2 class="side-label side-label--back">Back</h2>

  <!-- Front cover -->
  <svg class="cover cover--front" viewBox="0 0 962 1244" xmlns="http://www.w3.org/2000/svg">
    <defs>
      <linearGradient id="iris-tones" x1="0" y1="0" x2="1" y2="1">
        <stop offset="0" stop-color="#8a4a33"/>
        <stop offset="0.45" stop-color="#a7713a"/>
        <stop offset="0.75" stop-color="#c9a090"/>
        <stop offset="1" stop-color="#e6d4d4"/>
      </linearGradient>
    </defs>
    <rect class="cover-base" width="962" height="1244" fill="var(--crimson)"/>
    <polygon class="title-field" points="806,0 962,0 962,1244 903,1244 213,536" fill="var(--charcoal)"/>
    <polygon class="accent-stripe" points="213,536 903,1244 880,1244 199,549" fill="var(--crimson-deep)"/>
    <polygon class="eye-photo" role="img" aria-label="Fotografía en primer plano de un ojo con iris color avellana y pestañas"
             points="0,716 158,586 798,1244 0,1244" fill="url(#iris-tones)"/>

    <g class="institution">
      <circle class="institution-seal" cx="201" cy="96" r="63" fill="var(--paper)" stroke="var(--ink)" stroke-width="2"/>
      <line x1="39" y1="180" x2="364" y2="180" stroke="#d98a9c" stroke-width="2"/>
      <text class="institution-name" x="201" y="224" text-anchor="middle" textLength="325" lengthAdjust="spacingAndGlyphs">Universidad de Montehierro</text>
      <rect class="school-plate" x="45" y="248" width="313" height="76" fill="var(--paper)"/>
      <text class="school-name" x="201" y="295" text-anchor="middle" textLength="280" lengthAdjust="spacingAndGlyphs">Escuela de Doctorado Montehierro</text>
    </g>

    <line class="title-rule" x1="561" y1="389" x2="962" y2="389" stroke="var(--crimson)" stroke-width="6"/>
    <g class="title-text" text-anchor="middle">
      <text x="638" y="442" textLength="549" lengthAdjust="spacingAndGlyphs">"Diseño, desarrollo y</text>
      <text x="638" y="495" textLength="441" lengthAdjust="spacingAndGlyphs">validación de una</text>
      <text x="638" y="548" textLength="556" lengthAdjust="spacingAndGlyphs">encuesta para evaluar</text>
      <text x="638" y="601" textLength="582" lengthAdjust="spacingAndGlyphs">el compromiso visual y</text>
      <text x="638" y="654" textLength="543" lengthAdjust="spacingAndGlyphs">emocional subjetivos</text>
      <text x="638" y="707" textLength="419" lengthAdjust="spacingAndGlyphs">en pacientes con</text>
      <text x="638" y="760" textLength="365" lengthAdjust="spacingAndGlyphs">Queratocono"</text>
    </g>
    <line class="title-rule" x1="561" y1="781" x2="962" y2="781" stroke="var(--crimson)" stroke-width="6"/>

    <text class="author-spine" transform="translate(899 814) rotate(90)" textLength="362" lengthAdjust="spacingAndGlyphs">Iker Zurmendi</text>
  </svg>

  <!-- Back cover -->
  <svg class="cover cover--back" viewBox="0 0 964 1248" xmlns="http://www.w3.org/2000/svg">
    <rect class="cover-base" width="964" height="1248" fill="var(--slate)"/>
    <g class="bio-text" text-anchor="middle">
      <text x="481" y="101">"Iker Zurmendi, MD, es un Oftalmólogo</text>
      <text x="481" y="135">Subespecialista en Cirugía Refractiva de la</text>
      <text x="481" y="169">Universidad Tecnológica Cordillerana</text>
      <text x="481" y="203">(Colombia) y la Universidad de Montehierro</text>
      <text x="481" y="237">(España). Actualmente se desempeña como</text>
      <text x="481" y="271">miembro del Departamento de Córnea y</text>
      <text x="481" y="305">Cirugía Refractiva de la Clínica de</text>
      <text x="481" y="339">Oftalmología Miraluz y como director de</text>
      <text x="481" y="373">su propia compañía de emprendimiento</text>
      <text x="481" y="407">médico Silver Heron Surgical"</text>
    </g>
    <rect class="photo-slot" x="270" y="501" width="422" height="565" rx="40" fill="var(--paper)"/>
    <text class="photo-hint" x="481" y="778" text-anchor="middle">Author Photo here</text>
  </svg>
</main>
</body>
</html>
```